Need to drive pregnant women to my 3d4d ultrasound studio where i provide 4d ultrasound with hyperalistic imaging and gender reveals

Industry/Entity Type

Healthcare

Font styles to use
Decorative
Script

Requirements
Must have
• My Company name Cielo de Nuestra Espera 4D. EVERYTHING HAS TO BE IN SPANISH
Nice to have
• SIMPLE AND NOT TOO BUSY
Should not have
• website

```html
<!DOCTYPE html>
<html lang="es">
<head>
<meta charset="utf-8">
<title>Cielo de Nuestra Espera 4D</title>
<link rel="stylesheet" href="https://fonts.googleapis.com/css2?family=Dancing+Script:wght@600;700&family=Lilita+One&display=swap">
<style>
  :root {
    --backdrop: #a0a0a0;
    --paper: #ffffff;
    --ink: #050505;
    --silver: #8e8e8e;
    --silver-light: #d4d4d4;
    --sheen: #5c5c5e;
    --scan-deep: #6a3510;
    --scan-warm: #c0712a;
    --skin-deep: #c98b76;
    --skin-light: #f0c6b2;
  }
  * { margin: 0; padding: 0; box-sizing: border-box; }
  html, body {
    width: 1200px; height: 600px; overflow: hidden;
    background: var(--backdrop);
  }
  .banner {
    position: absolute;
    left: 79px; top: 154px;
    width: 1042px; height: 304px;
    background: var(--paper);
    box-shadow: 0 2px 4px rgba(0,0,0,0.35);
    overflow: hidden;
  }
  .banner-art { position: absolute; inset: 0; width: 100%; height: 100%; }
  .headline {
    position: absolute; left: 54px; top: 24px;
    font-family: "Lilita One", "Arial Black", sans-serif;
    font-weight: 400; color: var(--ink);
    line-height: 1;
  }
  .headline-top { display: block; font-size: 48px; letter-spacing: 1px; }
  .headline-main { display: block; font-size: 88px; margin-top: 0; letter-spacing: 0.5px; }
  .tagline {
    position: absolute; left: 72px; top: 212px; width: 400px;
    font-family: "Dancing Script", "Brush Script MT", cursive;
    font-weight: 700; font-size: 27px; line-height: 34px;
    color: var(--paper); text-align: center;
  }
</style>
</head>
<body>
  <section class="banner">
    <svg class="banner-art" viewBox="0 0 1042 304" xmlns="http://www.w3.org/2000/svg">
      <defs>
        <linearGradient id="silver-band" x1="0" x2="1" y1="0" y2="0">
          <stop offset="0" stop-color="var(--silver)"/>
          <stop offset="0.45" stop-color="var(--silver-light)"/>
          <stop offset="1" stop-color="var(--silver)"/>
        </linearGradient>
        <linearGradient id="dark-field" x1="0" x2="1" y1="0" y2="0">
          <stop offset="0" stop-color="var(--ink)"/>
          <stop offset="0.2" stop-color="var(--ink)"/>
          <stop offset="0.36" stop-color="var(--sheen)"/>
          <stop offset="0.55" stop-color="var(--ink)"/>
          <stop offset="1" stop-color="var(--ink)"/>
        </linearGradient>
        <radialGradient id="scan-tone" cx="0.45" cy="0.45" r="0.6">
          <stop offset="0" stop-color="var(--scan-warm)"/>
          <stop offset="1" stop-color="var(--scan-deep)"/>
        </radialGradient>
        <radialGradient id="newborn-tone" cx="0.5" cy="0.45" r="0.6">
          <stop offset="0" stop-color="var(--skin-light)"/>
          <stop offset="1" stop-color="var(--skin-deep)"/>
        </radialGradient>
      </defs>
      <path class="wave-band" fill="url(#silver-band)"
        d="M0,131 C90,175 190,194 290,190 C380,186 470,165 560,145 C700,120 900,140 1042,175 L1042,304 L0,304 Z"/>
      <path class="wave-field" fill="url(#dark-field)"
        d="M0,149 C90,190 190,204 290,200 C380,196 470,172 560,155 C700,135 900,165 1042,197 L1042,304 L0,304 Z"/>
      <g class="photo-frame">
        <circle cx="659" cy="152" r="120" fill="var(--silver-light)" stroke="var(--silver)" stroke-width="2"/>
        <circle cx="659" cy="152" r="114" fill="url(#scan-tone)" role="img" aria-label="Imagen de ecografía 4D del rostro del bebé"/>
      </g>
      <g class="photo-frame">
        <circle cx="878" cy="139" r="120" fill="var(--silver-light)" stroke="var(--silver)" stroke-width="2"/>
        <circle cx="878" cy="139" r="114" fill="url(#newborn-tone)" role="img" aria-label="Fotografía del bebé recién nacido dormido"/>
      </g>
    </svg>
    <h1 class="headline">
      <span class="headline-top">CIELO DE NUESTRA</span>
      <span class="headline-main">ESPERA 4D</span>
    </h1>
    <p class="tagline">Ecografía 4D con imágenes hiperrealistas y revelación de género</p>
  </section>
</body>
</html>
```